Website for an electrical contractor :)

We are after a web site which can show pictures of our jobs and our capability in a professional, creative and easily understood way.

----- Brightvale Electrical ------

We really want a visually good looking website with three sections

Section one:
'Completed projects'
We have a few pictures of jobs which we've completed and would like to show off with a brief description. (see uploads)

Section two:
'Our capabilities'
Just a list of what services we offer

Section three:
We would like a 'contact us' section which people can send us a short msg and upload a file for plans to be able to send to us. We would need their name, phone number and email details. We would also need a short privacy policy saying 'we do not disclose information to third parties'.
We also want to display our contact number and postal address

Good luck :)

Target Market(s)

Adults 25 years+
Business owners
Builders
Real estate agents

Industry/Entity Type

Electrical

Colors

Designer to choose colors to be used in the design.

Requirements
Must have
• Visually appealing
Easy to understand
In the 'Completed projects' section, must have a list for each project we do i can upload pictures for it.

```html
<!DOCTYPE html>
<html lang="en">
<head>
<meta charset="utf-8">
<title>Brightvale Electrical</title>
<link rel="stylesheet" href="https://fonts.googleapis.com/css2?family=Lato:ital,wght@0,400;0,700;1,400&family=Oswald:wght@400;500&family=Roboto:wght@300;400;500&display=swap">
<style>
:root{
  --red:#e3232a;
  --ink:#3d3d3d;
  --text:#555;
  --light:#f4f4f4;
  --line:#d9d9d9;
  --dark:#3b3b3b;
  --white:#fff;
}
*{box-sizing:border-box;margin:0;padding:0}
html,body{width:1200px;height:2695px;overflow:hidden}
body{position:relative;background:var(--white);font-family:'Lato',sans-serif;color:var(--text)}
.abs{position:absolute}
.center{left:0;width:1200px;text-align:center}

/* top bar */
.topbar{top:0;left:0;width:1200px;height:32px;background:#f0f0f0;border-bottom:1px solid #e2e2e2}
.topbar-item{position:absolute;top:0;height:32px;display:flex;align-items:center;gap:8px;font-size:12px;color:#666;border-left:1px solid #ddd;padding-left:16px}
.topbar-item svg{width:11px;height:11px;fill:#777}

/* header */
.header{top:32px;left:0;width:1200px;height:88px;background:var(--white)}
.brand{position:absolute;left:126px;top:18px;display:flex;align-items:center;gap:12px}
.brand-mark{width:40px;height:40px;border-radius:50%;background:var(--red)}
.brand-name{font-family:'Roboto',sans-serif;font-weight:400;font-size:40px;color:#444;line-height:1}
.nav{position:absolute;right:124px;top:40px;display:flex;gap:20px;font-family:'Roboto',sans-serif;font-size:12.5px;color:#444;text-transform:uppercase}

/* hero */
.hero{top:120px;left:0;width:1200px;height:523px;background:linear-gradient(180deg,#4a4540 0%,#7a6e62 35%,#8c8074 60%,#5e554c 100%)}
.hero-caption{position:absolute;left:212px;top:149px;width:785px;height:176px;background:rgba(60,60,60,.45);text-align:center;color:var(--white)}
.hero-title{font-family:'Oswald',sans-serif;font-weight:400;font-size:40px;margin-top:14px;letter-spacing:.2px}
.hero-text{font-family:'Oswald',sans-serif;font-size:14px;line-height:1.55;width:700px;margin:8px auto 0}
.btn{display:inline-flex;align-items:center;justify-content:center;gap:8px;background:var(--red);color:var(--white);font-family:'Roboto',sans-serif;font-size:13px}
.hero-btn{position:absolute;left:326px;top:127px;width:112px;height:32px;font-family:'Oswald',sans-serif;font-size:14px}
.hero-arrow{position:absolute;top:262px;width:38px;height:38px;border-radius:50%;display:flex;align-items:center;justify-content:center}
.hero-arrow svg{width:14px;height:14px}

/* section headings */
.section-title{font-family:'Roboto',sans-serif;font-weight:400;font-size:34px;color:var(--ink)}
.rule{width:46px;height:3px;background:var(--red);margin:12px auto 0}

/* about */
.about-text{left:124px;width:952px;top:734px;text-align:center;font-size:14.5px;line-height:26px;color:#444}
.about-btn{left:544px;top:832px;width:111px;height:33px}

/* projects */
.projects{top:902px;left:0;width:1200px;height:342px;background:linear-gradient(180deg,#6e6e6e,#8d8d8d 50%,#6a6a6a)}
.projects .section-title{color:var(--white)}
.project-card{position:absolute;top:106px;width:300px;height:200px;box-shadow:0 4px 10px rgba(0,0,0,.4)}
.card-one{left:124px;background:linear-gradient(160deg,#b8a49a,#8f7e75)}
.card-two{left:451px;background:linear-gradient(180deg,#6c6660,#9a8e82 60%,#6a6058)}
.card-three{left:776px;background:linear-gradient(180deg,#2f5fa8 0%,#5b86c4 50%,#8d8a80 75%,#6e6a62)}
.card-overlay{position:absolute;left:12px;top:12px;width:276px;height:176px;background:rgba(227,35,42,.82);color:var(--white);text-align:center}
.card-title{font-family:'Roboto',sans-serif;font-weight:500;font-size:13.5px;margin-top:45px}
.card-text{font-size:13px;line-height:19px;margin:10px 26px 0}
.card-btn{display:inline-block;margin-top:18px;width:86px;height:30px;line-height:30px;background:var(--white);color:var(--red);font-size:12px}
.slider-arrow{position:absolute;top:178px;width:38px;height:38px;background:var(--white);display:flex;align-items:center;justify-content:center}
.slider-arrow svg{width:14px;height:14px}

/* capabilities */
.capabilities{top:1244px;left:0;width:1200px;height:453px;background:var(--light)}
.cap-box{position:absolute;left:99px;top:114px;width:1002px;height:323px;background:#ececec;border:1px solid var(--line)}
.cap-heading{position:absolute;top:16px;width:462px;font-family:'Roboto',sans-serif;font-size:24px;color:#444;text-align:center;padding-bottom:8px;border-bottom:2px solid #c9c9c9}
.cap-list{position:absolute;top:68px;list-style:none;font-size:13px;line-height:19.8px;color:#555}
.cap-list li{padding-left:18px;position:relative}
.cap-list li::before{content:"»";position:absolute;left:0;color:var(--red);font-weight:700}
.cap-list li.active{color:var(--red)}

/* testimonials */
.quote-box{top:1787px;left:111px;width:968px;height:125px;background:#ececec;border:1px solid var(--line)}
.quote-box::after{content:"";position:absolute;right:140px;bottom:-14px;border-left:14px solid transparent;border-right:14px solid transparent;border-top:14px solid #ececec}
.avatar{position:absolute;left:32px;top:18px;width:92px;height:92px;border-radius:50%;background:linear-gradient(180deg,#5a4638,#a07a62)}
.quote-mark{position:absolute;font-family:'Roboto',sans-serif;font-size:44px;color:#666;line-height:1}
.quote-text{position:absolute;left:165px;top:16px;width:760px;font-style:italic;font-size:15.5px;line-height:28px;color:#555}
.dots{top:1928px;left:548px;display:flex;gap:4px}
.dots span{width:8px;height:8px;border-radius:50%;background:#777}
.author{top:1937px;left:860px;width:120px;text-align:center;font-style:italic;color:var(--red);font-size:13px;line-height:18px}

/* contact */
.contact{top:1983px;left:0;width:1200px;height:712px;background:var(--dark)}
.contact .section-title{color:var(--white);font-size:31px}
.field{position:absolute;left:305px;width:589px;height:36px;border:2px solid #d6d6d6;color:var(--white);font-size:11px;padding:10px 12px}
.upload{background:#eaeaea;color:#444;border-color:#eaeaea;padding-right:40px}
.upload-icon{position:absolute;right:0;top:0;width:28px;height:32px;background:#7d7d7d;display:flex;align-items:center;justify-content:center}
.send-btn{left:544px;top:452px;width:112px;height:35px;font-size:15px;font-weight:500}
.info-bar{left:126px;top:522px;width:948px;height:54px;background:var(--white);display:flex;align-items:center;justify-content:center;gap:36px;font-family:'Roboto',sans-serif;font-size:15.5px;color:#333}
.info-item{display:flex;align-items:center;gap:10px}
.info-item svg{width:15px;height:15px;fill:#333}
.footer-rule{left:126px;top:617px;width:948px;height:1px;background:#555}
.copyright{left:126px;top:651px;font-size:11px;color:#aaa}
.social{left:966px;top:651px;display:flex;gap:14px}
.social span{width:9px;height:9px;border-radius:50%;background:#bbb}
</style>
</head>
<body>

<div class="abs topbar">
  <div class="topbar-item" style="left:124px;width:122px">
    <svg viewBox="0 0 24 24"><path d="M6.6 10.8a15 15 0 0 0 6.6 6.6l2.2-2.2a1 1 0 0 1 1-.25 11.4 11.4 0 0 0 3.6.6 1 1 0 0 1 1 1V20a1 1 0 0 1-1 1A17 17 0 0 1 3 4a1 1 0 0 1 1-1h3.5a1 1 0 0 1 1 1c0 1.25.2 2.45.6 3.6a1 1 0 0 1-.25 1z"/></svg>0400 555 218</div>
  <div class="topbar-item" style="left:246px;width:124px">
    <svg viewBox="0 0 24 24"><path d="M6.6 10.8a15 15 0 0 0 6.6 6.6l2.2-2.2a1 1 0 0 1 1-.25 11.4 11.4 0 0 0 3.6.6 1 1 0 0 1 1 1V20a1 1 0 0 1-1 1A17 17 0 0 1 3 4a1 1 0 0 1 1-1h3.5a1 1 0 0 1 1 1c0 1.25.2 2.45.6 3.6a1 1 0 0 1-.25 1z"/></svg>08 9555 3164</div>
  <div class="topbar-item" style="left:370px;width:226px">
    <svg viewBox="0 0 24 24"><path d="M2 5h20v14H2zm2 2v.5l8 5 8-5V7zm0 3v7h16v-7l-8 5z"/></svg>hello@brightvaleelectrical.com.au</div>
  <div class="topbar-item" style="left:596px;width:368px;border-right:1px solid #ddd">
    <svg viewBox="0 0 24 24"><path d="M12 2a7 7 0 0 0-7 7c0 5 7 13 7 13s7-8 7-13a7 7 0 0 0-7-7zm0 9.5A2.5 2.5 0 1 1 12 6.5a2.5 2.5 0 0 1 0 5z"/></svg>P.O Box 417 Coral Bay W.A 6701 A.B.N: 48 210 736 905</div>
</div>

<header class="abs header">
  <div class="brand"><span class="brand-mark"></span><span class="brand-name">Brightvale</span></div>
  <nav class="nav"><span>Home</span><span>About us</span><span>Completed projects</span><span>Our capabilities</span><span>Testrimonial</span><span>Contact</span></nav>
</header>

<section class="abs hero" role="img" aria-label="Photo of a finished function room interior with lounge chairs and downlights">
  <div class="hero-caption">
    <h1 class="hero-title">Lorem Ipsum is simply dummy text of the printing</h1>
    <p class="hero-text">There are many variations of passages of Lorem Ipsum available, but the majority have suffered alteration in some form, by injected humour, or randomised words which don't look even slightly believable. If you are going to use a passage of Lorem Ipsum</p>
    <span class="btn hero-btn">Know More
      <svg width="12" height="12" viewBox="0 0 24 24"><circle cx="12" cy="12" r="11" fill="#fff"/><path d="M10 7l5 5-5 5" stroke="#e3232a" stroke-width="3" fill="none"/></svg></span>
  </div>
  <div class="hero-arrow" style="left:23px;background:#fff"><svg viewBox="0 0 24 24"><path d="M15 4l-8 8 8 8" stroke="#333" stroke-width="3" fill="none"/></svg></div>
  <div class="hero-arrow" style="left:1140px;background:var(--red)"><svg viewBox="0 0 24 24"><path d="M9 4l8 8-8 8" stroke="#fff" stroke-width="3" fill="none"/></svg></div>
</section>

<section>
  <div class="abs center" style="top:670px"><h2 class="section-title">About us</h2><div class="rule"></div></div>
  <p class="abs about-text">Lorem ipsum dolor sit amet conse ctetur adipisicing elit, sed do eiusmod tempor incididunt ut labore et dolore magna aliqua. Ut enim ad minim veniam, quis nostrud exercitation ullalaboris nisi ut aliquip ex ea commodo consequat.Lorem ipsum dolor sit amet conse ctetur adipisicing elit, sed do eiusmod tempor incididunt ut labore et</p>
  <span class="abs btn about-btn">Read More</span>
</section>

<section class="abs projects">
  <div class="abs center" style="top:22px"><h2 class="section-title">Completed projects</h2><div class="rule"></div></div>
  <div class="project-card card-one" role="img" aria-label="Project photo of a lounge area with armchairs">
    <div class="card-overlay">
      <div class="card-title">Lorem Ipsum is simply dummy text of the</div>
      <p class="card-text">There are many variations of passages of Lorem Ipsum available, but the majority</p>
      <span class="card-btn">Read More</span>
    </div>
  </div>
  <div class="project-card card-two" role="img" aria-label="Project photo of a function room with ceiling lighting"></div>
  <div class="project-card card-three" role="img" aria-label="Project photo of new townhouses under a blue sky"></div>
  <div class="slider-arrow" style="left:61px"><svg viewBox="0 0 24 24"><path d="M12 5l-7 7 7 7M19 5l-7 7 7 7" stroke="#333" stroke-width="2.4" fill="none"/></svg></div>
  <div class="slider-arrow" style="left:1101px"><svg viewBox="0 0 24 24"><path d="M5 5l7 7-7 7M12 5l7 7-7 7" stroke="#333" stroke-width="2.4" fill="none"/></svg></div>
</section>

<section class="abs capabilities">
  <div class="abs center" style="top:34px"><h2 class="section-title">Our capabilities</h2><div class="rule"></div></div>
  <div class="cap-box">
    <h3 class="cap-heading" style="left:20px">RESIDENTIAL</h3>
    <h3 class="cap-heading" style="left:514px">COMMERCIAL / INDUSTRIAL</h3>
    <ul class="cap-list" style="left:26px">
      <li class="active">24hr Support / faults</li><li>RCD (Safety Switch) installations</li><li>Smoke alarms</li><li>Power points</li><li>Lighting points</li><li>External lighting</li><li>Sensor lighting</li><li>Switching</li><li>Antennas and Arial points</li><li>Dimmers</li><li>Ceiling fans</li>
    </ul>
    <ul class="cap-list" style="left:270px">
      <li>Exhaust fans</li><li>Kitchen / Bathroom Projects</li><li>Re-wires</li><li>Smart wiring</li><li>Phone points</li><li>Data points</li><li>Mains/sub mains cabling</li><li>Switchboard installations</li><li>Compliance investigations</li><li>Concrete and wall chasing</li><li>Temporary builders site power</li>
    </ul>
    <ul class="cap-list" style="left:514px">
      <li>24hr Support / faults</li><li>Lighting/power design</li><li>Commercial lighting</li><li>Emergency and exit lighting</li><li>Led strip lighting</li><li>Energy efficient lighting</li><li>Temporary lighting</li><li>Illuminated signage</li><li>Switchboard relocations</li><li>Maintenance</li>
    </ul>
    <ul class="cap-list" style="left:759px;width:230px">
      <li>RCD installation</li><li>Phone/data points</li><li>Data cabinets</li><li>Data Networking</li><li>IDF installations/relocations</li><li>All power requirements</li><li>All three phase power require ments</li><li>Electrical rip outs / Disconnections</li><li>Thermal Imaging scans</li><li>Concrete and wall chasing</li>
    </ul>
  </div>
</section>

<section>
  <div class="abs center" style="top:1700px"><h2 class="section-title">Tesrimonials</h2><div class="rule"></div></div>
  <div class="abs quote-box">
    <div class="avatar" role="img" aria-label="Client portrait"></div>
    <span class="quote-mark" style="left:138px;top:6px">“</span>
    <p class="quote-text">Sed ut perspiciatis unde omnis iste natus error sit voluptatem accusantium doloremque laudantium, totam rem aperiam, eaque ipsa quae ab illo inventore veritatis et quasi architecto beatae vitae dicta sunt expli-cabo. Nemo enim ipsam voluptatem quia voluptas sit aspernatur aut odit aut fugit</p>
    <span class="quote-mark" style="left:740px;top:68px">”</span>
  </div>
  <div class="abs dots"><span></span><span></span><span></span><span></span></div>
  <div class="abs author">Daniel Crowe<br>usa</div>
</section>

<section class="abs contact">
  <div class="abs center" style="top:36px"><h2 class="section-title">Contact Us</h2><div class="rule"></div></div>
  <div class="field" style="top:111px">Name :</div>
  <div class="field" style="top:161px">Phone :</div>
  <div class="field" style="top:210px">Email Address :</div>
  <div class="field upload" style="top:260px">Upload File Your Plans
    <span class="upload-icon"><svg width="14" height="14" viewBox="0 0 24 24"><path d="M19 10a7 7 0 0 0-13.4-1.5A5 5 0 0 0 6 18.5h13a4.3 4.3 0 0 0 0-8.5zm-7 1l4 4h-3v3h-2v-3H8z" fill="#fff"/></svg></span></div>
  <div class="field" style="top:310px;height:113px">Message :</div>
  <span class="abs btn send-btn">SEND</span>
  <div class="abs info-bar">
    <span class="info-item"><svg viewBox="0 0 24 24"><path d="M12 2a7 7 0 0 0-7 7c0 5 7 13 7 13s7-8 7-13a7 7 0 0 0-7-7zm0 9.5A2.5 2.5 0 1 1 12 6.5a2.5 2.5 0 0 1 0 5z"/></svg>P.O Box 417 Coral Bay W.A 6701 A.B.N: 48 210 736 905</span>
    <span class="info-item"><svg viewBox="0 0 24 24"><path d="M6.6 10.8a15 15 0 0 0 6.6 6.6l2.2-2.2a1 1 0 0 1 1-.25 11.4 11.4 0 0 0 3.6.6 1 1 0 0 1 1 1V20a1 1 0 0 1-1 1A17 17 0 0 1 3 4a1 1 0 0 1 1-1h3.5a1 1 0 0 1 1 1c0 1.25.2 2.45.6 3.6a1 1 0 0 1-.25 1z"/></svg>0400 555 218</span>
    <span class="info-item"><svg viewBox="0 0 24 24"><path d="M6.6 10.8a15 15 0 0 0 6.6 6.6l2.2-2.2a1 1 0 0 1 1-.25 11.4 11.4 0 0 0 3.6.6 1 1 0 0 1 1 1V20a1 1 0 0 1-1 1A17 17 0 0 1 3 4a1 1 0 0 1 1-1h3.5a1 1 0 0 1 1 1c0 1.25.2 2.45.6 3.6a1 1 0 0 1-.25 1z"/></svg>08 9555 3164</span>
  </div>
  <div class="abs footer-rule"></div>
  <p class="abs copyright">© Copy Right 2013-2015 Brightvale Electrical . &nbsp; | &nbsp; Privacy Policy &nbsp; | &nbsp; All rights reserved.</p>
  <div class="abs social"><span></span><span></span><span></span><span></span><span></span></div>
</section>

</body>
</html>
```